IT Consulting Business needs a web design

We need a web design for an IT Consulting company called "Vorensk". We want to replace the existing web site (www.vorensk-example.com) with a new design. Our services are IT Consulting, IT Training, IT Outsourcing.
We would like to see designs that communicate "Trusted IT Advisor" with modern & bold design.

We would like to see the design of 2 pages:
1. Home page (www.vorensk-example.com)
2. The detail page (http://www.vorensk-example.com/index_files/consulting.htm)

Industry/Entity Type

Business

```html
<!DOCTYPE html>
<html lang="en">
<head>
<meta charset="utf-8">
<title>Vorensk – IT Consulting</title>
<link href="https://fonts.googleapis.com/css2?family=Arimo:wght@400;700&family=Ubuntu:wght@300;400&display=swap" rel="stylesheet">
<style>
:root{
  --red:#d01b1e;
  --red-dark:#a30c10;
  --red-light:#ee3b3c;
  --blue:#0b57b0;
  --blue-nav:#1e6fd6;
  --blue-nav-dark:#1250b0;
  --page:#f4f4f4;
  --text:#444;
  --heading:#3a3a3a;
  --rule:#cfcfcf;
  --footer:#2b2b2b;
}
*{margin:0;padding:0;box-sizing:border-box}
html,body{width:1133px;height:1200px;overflow:hidden}
body{background:var(--page);font-family:"Ubuntu",sans-serif;color:var(--text);position:relative}
.band{position:absolute;left:0;top:0;width:1133px;height:388px;
  background:radial-gradient(ellipse at 50% 20%,var(--red-light) 0%,var(--red) 45%,var(--red-dark) 100%)}
.logo{position:absolute;left:147px;top:0;width:191px;height:112px;background:#fff;
  clip-path:polygon(0 0,100% 0,100% 78%,50% 100%,0 78%);
  display:flex;align-items:center;justify-content:center;padding-bottom:24px}
.logo span{font-family:"Arimo",sans-serif;font-weight:700;font-size:34px;color:var(--blue);letter-spacing:-0.5px}
.contact{position:absolute;top:28px;right:147px;display:flex;gap:28px;color:#fff;font-size:14.5px}
.contact span{display:flex;align-items:center;gap:7px}
.nav{position:absolute;left:468px;top:70px;width:517px;height:44px;border-radius:6px;
  background:linear-gradient(var(--blue-nav),var(--blue-nav-dark));display:flex;align-items:center;padding-left:12px}
.nav a{color:#dbe8ff;text-decoration:none;font-size:13.5px;padding:0 15px;border-left:1px solid rgba(255,255,255,.35);line-height:16px}
.nav a:first-child{border-left:none;color:#fff}
.hero{position:absolute;left:147px;top:138px;width:838px;height:349px;
  background:linear-gradient(90deg,#1a2230 0%,#2b3548 40%,#2a6fc0 70%,#3a9ae8 100%)}
.hero-shadow{position:absolute;top:487px;height:22px;width:360px;
  background:radial-gradient(ellipse at 50% 0,rgba(0,0,0,.35),transparent 70%)}
.values{position:absolute;left:147px;top:530px;width:838px;height:44px;border-top:1px solid var(--rule);border-bottom:1px solid var(--rule)}
.values-tag{position:absolute;left:0;top:-1px;height:44px;width:139px;background:var(--red);color:#fff;
  font-family:"Arimo",sans-serif;font-weight:700;font-size:16px;display:flex;align-items:center;padding-left:14px;
  clip-path:polygon(0 0,88% 0,100% 50%,88% 100%,0 100%)}
.value{position:absolute;top:13px;font-family:"Arimo",sans-serif;font-weight:700;font-size:12.5px;color:#666;display:flex;align-items:center;gap:10px}
.service{position:absolute;top:600px;width:264px}
.service h2,.section-title{font-family:"Arimo",sans-serif;font-weight:700;font-size:17.5px}
.service h2 .lead{color:var(--red)}
.service h2 .rest{color:var(--blue)}
.frame{border:1px solid #d6d6d6;background:#fff;padding:5px;margin-top:7px}
.photo{height:120px}
.service p{font-size:11px;line-height:13.6px;margin-top:12px;text-align:justify;height:54px}
.btn{display:inline-block;background:var(--red);color:#fff;font-size:13px;border-radius:3px;width:62px;height:26px;line-height:26px;text-align:center;margin-top:11px}
.divider{position:absolute;left:147px;top:882px;width:838px;height:1px;background:var(--rule)}
.section-title{position:absolute;color:var(--heading)}
.trusted-frame{position:absolute;left:147px;top:930px;width:257px;height:158px;border:1px solid #d6d6d6;background:#fff;padding:6px}
.trusted-text{position:absolute;left:419px;top:928px;width:303px;font-size:11px;line-height:15.7px}
.expertise{position:absolute;left:755px;top:935px;width:230px;list-style:none;font-size:11px;line-height:18px}
.expertise li{position:relative;padding-left:23px;margin-bottom:8px}
.expertise svg{position:absolute;left:2px;top:5px}
.footer{position:absolute;left:0;top:1117px;width:1133px;height:83px;background:var(--footer);color:#fff;font-family:"Arimo",sans-serif;font-size:12px}
.footer-nav{position:absolute;left:146px;top:23px;display:flex}
.footer-nav a{color:#fff;text-decoration:none}
.footer-nav a.current{color:var(--red-light)}
.footer-nav .sep{margin:0 10px}
.copyright{position:absolute;left:146px;top:42px}
.social{position:absolute;right:148px;top:17px;display:flex;gap:5px}
.social span{width:25px;height:25px;background:var(--red);border-radius:3px;display:block}
</style>
</head>
<body>
<div class="band"></div>

<div class="logo"><span>Vorensk</span></div>

<div class="contact">
  <span><svg width="16" height="12" viewBox="0 0 16 12"><path d="M1 4c0-2 3-3 7-3s7 1 7 3l-3 1-1-2H5L4 5zM3 6h10l1 5H2z" fill="#fff"/></svg>1300 555 019</span>
  <span><svg width="13" height="9" viewBox="0 0 13 9"><rect width="13" height="9" fill="#fff"/><path d="M0 0l6.5 5L13 0" stroke="#c33" fill="none"/></svg>info@vorensk-example.com</span>
</div>

<nav class="nav">
  <a>Home</a><a>About us</a><a>Services</a><a>Expertises</a><a>Careers</a><a>Contact Us</a>
</nav>

<div class="hero" role="img" aria-label="Businessman in a suit writing the words technology, information, quality and success on a glowing blue screen"></div>
<div class="hero-shadow" style="left:170px"></div>
<div class="hero-shadow" style="left:600px"></div>

<div class="values">
  <div class="values-tag">CORE VALUE</div>
  <div class="value" style="left:178px"><svg width="9" height="12"><path d="M1 1l6 5-6 5" stroke="#e01b1e" stroke-width="2.5" fill="none"/></svg>QUALITY CONSCIOUS</div>
  <div class="value" style="left:414px"><svg width="9" height="12"><path d="M1 1l6 5-6 5" stroke="#e01b1e" stroke-width="2.5" fill="none"/></svg>CUSTOMER FOCUS</div>
  <div class="value" style="left:629px"><svg width="9" height="12"><path d="M1 1l6 5-6 5" stroke="#e01b1e" stroke-width="2.5" fill="none"/></svg>COMMITTED</div>
</div>

<section class="service" style="left:147px">
  <h2><span class="lead">Consulting</span> <span class="rest">Services</span></h2>
  <div class="frame"><div class="photo" role="img" aria-label="Team of colleagues reviewing work at a computer" style="background:linear-gradient(90deg,#3b4a3a,#c9c2b0 45%,#d8c690 75%,#a8b27a)"></div></div>
  <p>Our experienced, certified professionals provides IT consulting using industry recommended practices. We are specialized in Nimbra Business Productivity Platform using Nimbra Portal..</p>
  <span class="btn">more</span>
</section>

<section class="service" style="left:434px">
  <h2><span class="lead">Training</span> <span class="rest">Services</span></h2>
  <div class="frame"><div class="photo" role="img" aria-label="Hand with a pen pointing at charts on a screen" style="background:linear-gradient(90deg,#8a95a3,#2e3f5a 40%,#a9c1dd 65%,#5a7396)"></div></div>
  <p>Our certified trainers provide in-house training for Vorensk original courses as well as customized training courses that suit your organization needs. On-Site training..</p>
  <span class="btn">more</span>
</section>

<section class="service" style="left:722px">
  <h2><span class="lead">Solution</span> <span class="rest">Services</span></h2>
  <div class="frame"><div class="photo" role="img" aria-label="Hands using a phone and a tablet showing business charts" style="background:linear-gradient(90deg,#e4dccb,#c9c4b8 45%,#b58a5a 80%,#d8b990)"></div></div>
  <p>Vorensk's unique solution services offer customers with the benefits of our expert consultants in designing, deploying, and implementing our solutions. Customers who want to have the,</p>
  <span class="btn">more</span>
</section>

<div class="divider"></div>

<h2 class="section-title" style="left:147px;top:899px">Most Trusted IT Consultant</h2>
<div class="trusted-frame"><div role="img" aria-label="Smiling support consultant with a headset in front of a team" style="height:100%;background:linear-gradient(90deg,#b9ccdc,#dfe7ee 40%,#8394a8 70%,#c8d6e2)"></div></div>
<p class="trusted-text">We are experienced, certified professionals who are experts at Information Technology (IT) consulting, solution design &amp; development, and training for medium-size businesses and large enterprises. We are committed to helping our clients quickly achieve the most appropriate solution with sustainable ROI. We are focusing on Nimbra Technologies for large organizations. We offer the agility of a smaller firm, the quality of larger firms.</p>
<span class="btn" style="position:absolute;left:420px;top:1052px;margin:0">more</span>

<h2 class="section-title" style="left:755px;top:898px">Our Expertises</h2>
<ul class="expertise">
  <li><svg width="9" height="9"><g fill="#e01b1e"><rect width="3" height="3"/><rect x="5" width="3" height="3"/><rect y="5" width="3" height="3"/><rect x="5" y="5" width="3" height="3"/></g></svg>Nimbra Portal Technologies</li>
  <li><svg width="9" height="9"><g fill="#e01b1e"><rect width="3" height="3"/><rect x="5" width="3" height="3"/><rect y="5" width="3" height="3"/><rect x="5" y="5" width="3" height="3"/></g></svg>Business Intelligence with Nimbra Data Server</li>
  <li><svg width="9" height="9"><g fill="#e01b1e"><rect width="3" height="3"/><rect x="5" width="3" height="3"/><rect y="5" width="3" height="3"/><rect x="5" y="5" width="3" height="3"/></g></svg>Enterprise Integration with Flowlink Server</li>
  <li><svg width="9" height="9"><g fill="#e01b1e"><rect width="3" height="3"/><rect x="5" width="3" height="3"/><rect y="5" width="3" height="3"/><rect x="5" y="5" width="3" height="3"/></g></svg>Corvane Development</li>
  <li><svg width="9" height="9"><g fill="#e01b1e"><rect width="3" height="3"/><rect x="5" width="3" height="3"/><rect y="5" width="3" height="3"/><rect x="5" y="5" width="3" height="3"/></g></svg>Tessary Workflow</li>
</ul>

<footer class="footer">
  <div class="footer-nav">
    <a class="current">Home</a><span class="sep">|</span><a>About Us</a><span class="sep">|</span><a>Services</a><span class="sep">|</span><a>Careers</a><span class="sep">|</span><a>Expertises</a><span class="sep">|</span><a>Contact Us</a>
  </div>
  <div class="copyright">Vorensk © 2013. All Rights Reserved.</div>
  <div class="social"><span></span><span></span><span></span></div>
</footer>
</body>
</html>
```